Lumavento business card

We need a modern business card - With our 4 colors - See web: www.lumavento.dk

I have attached logo and som old business Cards we have - Lets Make the new ones shine...:-) -

Industry/Entity Type

Business

Requirements
Must have
• the logo with lumavento only,

```html
<!DOCTYPE html>
<html lang="da">
<head>
<meta charset="utf-8">
<title>Lumavento – visitkort</title>
<link rel="stylesheet" href="https://fonts.googleapis.com/css2?family=Source+Sans+3:wght@300;400;700&display=swap">
<style>
  :root {
    --backdrop: #34302c;
    --card: #0b0b0b;
    --lime: #9cc83a;
    --orange: #f39325;
    --purple: #7b3f98;
    --pink: #e5337f;
    --grey: #b9b9b9;
  }
  * { margin: 0; padding: 0; box-sizing: border-box; }
  html, body { width: 1200px; height: 900px; overflow: hidden; }
  body {
    background: var(--backdrop);
    font-family: "Source Sans 3", sans-serif;
    position: relative;
  }
  .card {
    position: absolute;
    top: 275px;
    width: 540px;
    height: 350px;
    background: var(--card);
    box-shadow: 0 10px 30px rgba(0,0,0,.45);
  }
  .card--front { left: 40px; }
  .card--back { left: 620px; }

  /* front */
  .brand-block {
    position: absolute;
    left: 0; top: 0;
    width: 250px; height: 100%;
    display: flex; align-items: center; justify-content: center; gap: 10px;
  }
  .brand-dot {
    width: 14px; height: 14px; border-radius: 50%;
    background: var(--lime);
  }
  .brand-name {
    color: var(--lime);
    font-size: 30px;
    font-weight: 300;
    letter-spacing: 3px;
  }
  .divider {
    position: absolute;
    left: 252px; top: 30px;
    width: 1px; height: 290px;
    background: linear-gradient(to bottom, rgba(243,147,37,0), rgba(243,147,37,.45), rgba(243,147,37,0));
  }
  .details {
    position: absolute;
    left: 280px; top: 56px;
    color: var(--lime);
    font-size: 15px;
    line-height: 1.3;
  }
  .person-name {
    color: var(--orange);
    font-size: 21px;
    font-weight: 700;
  }
  .person-title { margin-bottom: 26px; }
  .address { margin-bottom: 18px; }
  .contact-list { list-style: none; }
  .contact-list li {
    display: flex; align-items: center; gap: 10px;
    margin-bottom: 5px;
  }
  .contact-list svg { width: 12px; height: 12px; flex: none; }

  /* back */
  .back-brand {
    position: absolute;
    left: 160px; top: 120px;
    width: 250px;
    text-align: center;
  }
  .back-brand .brand-name {
    display: block;
    font-size: 26px;
    color: var(--grey);
    letter-spacing: 5px;
  }
  .brand-rule {
    height: 3px;
    background: var(--lime);
    margin: 14px 0 8px;
  }
  .tagline {
    color: var(--grey);
    font-size: 14px;
    font-weight: 300;
  }
</style>
</head>
<body>
  <section class="card card--front">
    <div class="brand-block">
      <span class="brand-dot"></span>
      <span class="brand-name">lumavento</span>
    </div>
    <div class="divider"></div>
    <div class="details">
      <p class="person-name">Sigrid Holmgaard</p>
      <p class="person-title">Salgsdirektør</p>
      <p class="address">Lyngbyvej 48 - 2100<br>Østerbro - Tlf. 31 42 67 80</p>
      <ul class="contact-list">
        <li>
          <svg viewBox="0 0 12 12" aria-hidden="true"><path fill="#f39325" d="M2.5 0.5l2 2.2-1 1.3c.7 1.5 1.9 2.7 3.5 3.5l1.3-1 2.2 2-1.2 2c-4.5-.3-8-3.8-8.3-8.3z"/></svg>
          +45 61 72 83 94
        </li>
        <li>
          <svg viewBox="0 0 12 12" aria-hidden="true"><rect x="0.5" y="2" width="11" height="8" fill="#f39325"/><path d="M0.5 2l5.5 4.5L11.5 2" fill="none" stroke="#0b0b0b" stroke-width="1"/></svg>
          sh@lumavento.dk
        </li>
        <li>
          <svg viewBox="0 0 12 12" aria-hidden="true"><circle cx="6" cy="6" r="5.5" fill="#f39325"/><path d="M0.5 6h11M6 .5c-2.5 3-2.5 8 0 11M6 .5c2.5 3 2.5 8 0 11" fill="none" stroke="#0b0b0b" stroke-width=".8"/></svg>
          www.lumavento.dk
        </li>
      </ul>
    </div>
  </section>

  <section class="card card--back">
    <div class="back-brand">
      <span class="brand-name">lumavento</span>
      <div class="brand-rule"></div>
      <p class="tagline">Medier til unge</p>
    </div>
  </section>
</body>
</html>
```